Powerpoint contest

We need to re-design our powerpoints to be much more consistent. All the details are mentioned here. I have more than 30 slides to be created in all.

https://www.pagevault.example/kradnex/All-Powerpoints-fa5a253bd6ed4bc5924a937df39dbb80

Requirements
Must have
• Colors should be greyscale and vexacell pink (ea0a8e) used in small amounts just for accents.

```html
<!DOCTYPE html>
<html lang="en">
<head>
<meta charset="utf-8">
<title>Kradnex Presentation Templates</title>
<link rel="stylesheet" href="https://fonts.googleapis.com/css2?family=Oswald:wght@700&family=Poppins:wght@300;400;500;600;700&display=swap">
<style>
  :root {
    --pink: #e3137f;
    --blue: #1a9fe0;
    --ink: #0d0d0d;
    --text: #2a2a2a;
    --muted: #5a5a5a;
    --paper: #ffffff;
    --stripe: #ededed;
    --stage-top: #c6c6c8;
    --stage-floor: #dcdcdd;
    --board: #e6e6e6;
    --photo-dark: #3a3230;
    --photo-mid: #5b514c;
  }
  * { box-sizing: border-box; margin: 0; padding: 0; }
  html, body { width: 698px; height: 1200px; overflow: hidden; }
  body { font-family: 'Poppins', sans-serif; color: var(--text); background: var(--board); position: relative; }

  .hero-stage {
    position: absolute; left: 0; top: 0; width: 698px; height: 403px;
    background: linear-gradient(180deg, var(--stage-top) 0%, #cfcfd1 78%, var(--stage-floor) 79%, var(--stage-floor) 100%);
  }
  .hero-stage .slide {
    left: 171px; top: 110px; transform: scale(1.156); transform-origin: 0 0;
    box-shadow: 0 6px 16px rgba(0,0,0,.25);
  }

  .slide {
    position: absolute; width: 307px; height: 230px; background: var(--paper);
    overflow: hidden; box-shadow: 0 5px 8px rgba(0,0,0,.18);
  }
  .col-left { left: 27px; }
  .col-right { left: 362px; }
  .row-1 { top: 431px; }
  .row-2 { top: 682px; }
  .row-3 { top: 934px; }

  /* cover */
  .cover-photo { position: absolute; inset: 0; background: linear-gradient(135deg, var(--photo-dark) 0%, var(--photo-mid) 45%, #4a4543 70%, #2e2a29 100%); }
  .cover-photo::after { content: ""; position: absolute; inset: 0; background: rgba(20,18,18,.35); }
  .cover-title {
    position: absolute; left: 0; right: 0; top: 44px; text-align: center;
    font-family: 'Oswald', sans-serif; font-weight: 700; font-size: 29px; line-height: 32px;
    color: #fff; letter-spacing: -.2px;
  }
  .cover-sub {
    position: absolute; left: 40px; right: 40px; top: 78px; text-align: center;
    font-size: 5.6px; line-height: 8px; color: #f1f1f1; font-weight: 300;
  }
  .cover-curve { position: absolute; left: 0; top: 0; }
  .cover-brand {
    position: absolute; left: 0; right: 0; top: 184px; display: flex; justify-content: center; align-items: center; gap: 9px;
  }
  .cover-brand .mark { width: 20px; height: 20px; border-radius: 50%; background: var(--pink); }
  .cover-brand .name { font-size: 28px; font-weight: 700; color: var(--ink); line-height: 30px; letter-spacing: .3px; }

  /* common header/footer */
  .slide-head { position: absolute; left: 0; right: 0; top: 0; height: 30px; }
  .slide-head .bullet { position: absolute; left: 2px; top: 13px; width: 7px; height: 7px; border-radius: 50%; background: var(--pink); }
  .slide-head h2 { position: absolute; left: 14px; top: 10px; font-size: 9px; font-weight: 400; color: var(--ink); line-height: 12px; }
  .slide-head .brand { position: absolute; right: 10px; top: 10px; display: flex; align-items: center; gap: 3px; }
  .slide-head .brand .mark { width: 6px; height: 6px; border-radius: 50%; background: var(--pink); }
  .slide-head .brand .name { font-size: 10px; font-weight: 700; color: var(--ink); line-height: 12px; }
  .slide-head .rule { position: absolute; left: 11px; right: 11px; top: 28px; border-top: 1px dotted var(--pink); }

  .slide-foot { position: absolute; left: 0; right: 0; bottom: 0; height: 17px; background: var(--ink); border-top: 1px solid #bdbdbd; }
  .slide-foot .meta { position: absolute; right: 12px; top: 3px; display: flex; align-items: center; gap: 3px; font-size: 5.6px; color: #fff; line-height: 9px; }
  .slide-foot .globe { width: 9px; height: 9px; }
  .slide-foot .sep { margin: 0 3px; }

  /* agenda */
  .agenda-list { position: absolute; left: 18px; top: 56px; list-style: none; }
  .agenda-list li { display: flex; height: 17.2px; align-items: center; font-size: 5.8px; color: var(--text); }
  .agenda-list .item { width: 75px; }
  .agenda-list .dash { width: 46px; letter-spacing: .6px; color: var(--muted); }
  .agenda-list .num { width: 10px; }
  .agenda-visual { position: absolute; left: 160px; top: 50px; width: 140px; height: 150px; }
  .agenda-visual .frame { position: absolute; left: 10px; top: 12px; width: 120px; height: 126px; border: 3px solid #333; transform: rotate(-15deg); }
  .agenda-visual .photo { position: absolute; left: 8px; top: 10px; width: 124px; height: 128px; border-radius: 48% 52% 45% 55%; background: radial-gradient(circle at 55% 40%, #a7c6d6 0%, #5d8aa6 45%, #2f5a80 100%); }

  /* heading one */
  .step-ring { position: absolute; top: 0; left: 0; }
  .step-label { position: absolute; width: 50px; text-align: center; font-size: 6.7px; color: var(--text); font-weight: 500; top: 100px; }
  .body-copy { position: absolute; font-size: 5px; line-height: 7.1px; color: var(--text); text-align: justify; }
  .copy-one { left: 20px; top: 150px; width: 267px; }

  /* heading two */
  .feature-band { position: absolute; height: 31px; background: var(--stripe); }
  .feature { position: absolute; width: 90px; }
  .feature h3 { font-size: 5.8px; font-weight: 600; color: var(--pink); line-height: 7px; }
  .feature p { font-size: 3.9px; line-height: 5.4px; color: var(--text); }
  .feature.left { text-align: right; }
  .hub-visual { position: absolute; left: 0; top: 0; }
  .phone-screen { position: absolute; left: 130px; top: 88px; width: 47px; height: 98px; background: linear-gradient(160deg, #c9a37a 0%, #e8e2d8 45%, #8c8f93 100%); }

  /* heading three */
  .tablet-visual { position: absolute; left: 8px; top: 48px; width: 150px; height: 150px; }
  .tablet-visual .photo { position: absolute; left: 10px; top: 12px; width: 130px; height: 126px; border-radius: 10% 14% 12% 16%; background: linear-gradient(150deg, #e9ecf0 0%, #c8ced6 55%, #6f6a66 100%); transform: rotate(-10deg); }
  .tablet-visual .frame { position: absolute; left: 12px; top: 14px; width: 128px; height: 124px; border: 3px solid #222; transform: rotate(-14deg); }
  .copy-three { left: 167px; width: 119px; }

  /* heading four */
  .map-area { position: absolute; left: 26px; top: 46px; width: 255px; height: 150px; border-radius: 40%; background: radial-gradient(ellipse at center, #f1f1f1 0%, #f7f7f7 60%, #ffffff 100%); }
  .milestone-title { position: absolute; width: 40px; text-align: center; font-size: 5.4px; font-weight: 500; color: var(--ink); }
</style>
</head>
<body>

<!-- Featured cover -->
<section class="hero-stage">
  <article class="slide cover">
    <div class="cover-photo" role="img" aria-label="Darkened photo of a person typing on a laptop at a desk"></div>
    <h1 class="cover-title">HEADLINE GOES HERE</h1>
    <p class="cover-sub">Lorem Ipsum is simply dummy text of the printing and typesetting industry. Lorem Ipsum has been the industry's standard dummy text.</p>
    <svg class="cover-curve" width="307" height="230" viewBox="0 0 307 230">
      <path d="M0 214 Q130 124 307 186 L307 230 L0 230 Z" fill="#ffffff"/>
      <path d="M0 214 Q130 124 307 186 L307 190 Q140 136 10 230 L0 230 Z" fill="#e3137f"/>
    </svg>
    <div class="cover-brand"><span class="mark"></span><span class="name">Kradnex</span></div>
  </article>
</section>

<!-- Cover -->
<article class="slide cover col-left row-1">
  <div class="cover-photo" role="img" aria-label="Darkened photo of a person typing on a laptop at a desk"></div>
  <h1 class="cover-title">HEADLINE GOES HERE</h1>
  <p class="cover-sub">Lorem Ipsum is simply dummy text of the printing and typesetting industry. Lorem Ipsum has been the industry's standard dummy text.</p>
  <svg class="cover-curve" width="307" height="230" viewBox="0 0 307 230">
    <path d="M0 214 Q130 124 307 186 L307 230 L0 230 Z" fill="#ffffff"/>
    <path d="M0 214 Q130 124 307 186 L307 190 Q140 136 10 230 L0 230 Z" fill="#e3137f"/>
  </svg>
  <div class="cover-brand"><span class="mark"></span><span class="name">Kradnex</span></div>
</article>

<!-- Agenda -->
<article class="slide col-right row-1">
  <header class="slide-head"><span class="bullet"></span><h2>Agenda</h2><div class="brand"><span class="mark"></span><span class="name">Kradnex</span></div><div class="rule"></div></header>
  <ol class="agenda-list">
    <li><span class="item">Heading One Goes Here</span><span class="dash">----------</span><span class="num">3</span></li>
    <li><span class="item">Heading Two Goes Here</span><span class="dash">----------</span><span class="num">4</span></li>
    <li><span class="item">Heading Three Goes Here</span><span class="dash">----------</span><span class="num">5</span></li>
    <li><span class="item">Heading Four Goes Here</span><span class="dash">----------</span><span class="num">6</span></li>
    <li><span class="item">Heading Five Goes Here</span><span class="dash">----------</span><span class="num">7</span></li>
    <li><span class="item">Heading Six Goes Here</span><span class="dash">----------</span><span class="num">8</span></li>
    <li><span class="item">Heading Seven Goes Here</span><span class="dash">----------</span><span class="num">9</span></li>
    <li><span class="item">Heading Eight Goes Here</span><span class="dash">----------</span><span class="num">10</span></li>
  </ol>
  <div class="agenda-visual">
    <div class="photo" role="img" aria-label="Blue-toned photo of a smiling woman using a tablet with a rising bar chart"></div>
    <div class="frame"></div>
  </div>
  <footer class="slide-foot"><div class="meta"><svg class="globe" viewBox="0 0 10 10"><circle cx="5" cy="5" r="4.5" fill="#fff"/><circle cx="5" cy="5" r="3.4" fill="#1a9fe0"/><path d="M1.6 5h6.8M5 1.6v6.8M2.4 3.3h5.2M2.4 6.7h5.2" stroke="#fff" stroke-width=".5"/></svg><span>www.kradnex.com</span><span class="sep">|</span><span>Page : 2</span></div></footer>
</article>

<!-- Heading One -->
<article class="slide col-left row-2">
  <header class="slide-head"><span class="bullet"></span><h2>Heading One Goes Here</h2><div class="brand"><span class="mark"></span><span class="name">Kradnex</span></div><div class="rule"></div></header>
  <svg class="step-ring" width="307" height="150" viewBox="0 0 307 150">
    <g fill="none" stroke="#e3137f" stroke-width="1">
      <line x1="95" y1="92" x2="118" y2="92"/>
      <line x1="186" y1="92" x2="210" y2="92"/>
    </g>
    <g fill="#fff" stroke="#e3137f" stroke-width="1">
      <circle cx="96" cy="92" r="2"/><circle cx="117" cy="92" r="2"/>
      <circle cx="187" cy="92" r="2"/><circle cx="209" cy="92" r="2"/>
    </g>
    <g id="step">
      <circle cx="61.5" cy="92" r="34" fill="none" stroke="#e3137f" stroke-width="1" stroke-dasharray="1.2 1.6"/>
      <path d="M27.5 92 A34 34 0 0 1 85 67" fill="none" stroke="#e3137f" stroke-width="1.2"/>
      <circle cx="61.5" cy="92" r="29" fill="none" stroke="#1a9fe0" stroke-width="4"/>
    </g>
    <g transform="translate(90.5 0)">
      <circle cx="61.5" cy="92" r="34" fill="none" stroke="#e3137f" stroke-width="1" stroke-dasharray="1.2 1.6"/>
      <path d="M95.5 92 A34 34 0 0 1 38 117" fill="none" stroke="#e3137f" stroke-width="1.2"/>
      <circle cx="61.5" cy="92" r="29" fill="none" stroke="#1a9fe0" stroke-width="4"/>
    </g>
    <g transform="translate(182.5 0)">
      <circle cx="61.5" cy="92" r="34" fill="none" stroke="#e3137f" stroke-width="1" stroke-dasharray="1.2 1.6"/>
      <path d="M27.5 92 A34 34 0 0 1 85 67" fill="none" stroke="#e3137f" stroke-width="1.2"/>
      <circle cx="61.5" cy="92" r="29" fill="none" stroke="#1a9fe0" stroke-width="4"/>
    </g>
    <g fill="none" stroke="#222" stroke-width="1">
      <rect x="55" y="78" width="13" height="8"/><path d="M57 84l3-3 2 2 4-4"/>
      <rect x="145.5" y="78" width="13" height="8"/><path d="M147.5 84l3-3 2 2 4-4"/>
      <rect x="237.5" y="78" width="13" height="8"/><path d="M239.5 84l3-3 2 2 4-4"/>
    </g>
    <g fill="#222">
      <circle cx="57" cy="88.5" r="1.5"/><circle cx="66" cy="88.5" r="1.5"/>
      <circle cx="147.5" cy="88.5" r="1.5"/><circle cx="156.5" cy="88.5" r="1.5"/>
      <circle cx="239.5" cy="88.5" r="1.5"/><circle cx="248.5" cy="88.5" r="1.5"/>
    </g>
  </svg>
  <span class="step-label" style="left:36.5px;">Text Here</span>
  <span class="step-label" style="left:127px;">Text Here</span>
  <span class="step-label" style="left:219px;">Text Here</span>
  <p class="body-copy copy-one">Lorem Ipsum is simply dummy text of the printing and typesetting industry. Lorem Ipsum has been the industry's standard dummy text ever since the 1500s, when an unknown printer took a galley of type and scrambled it to make a type specimen book. It has survived not only five centuries, but also the leap into electronic typesetting, remaining essentially unchanged. It was popularised in the 1960s with the release of Letraset sheets containing Lorem Ipsum.when an unknown printer took a galley of type.</p>
  <footer class="slide-foot"><div class="meta"><svg class="globe" viewBox="0 0 10 10"><circle cx="5" cy="5" r="4.5" fill="#fff"/><circle cx="5" cy="5" r="3.4" fill="#1a9fe0"/><path d="M1.6 5h6.8M5 1.6v6.8M2.4 3.3h5.2M2.4 6.7h5.2" stroke="#fff" stroke-width=".5"/></svg><span>www.kradnex.com</span><span class="sep">|</span><span>Page : 3</span></div></footer>
</article>

<!-- Heading Two -->
<article class="slide col-right row-2">
  <header class="slide-head"><span class="bullet"></span><h2>Heading Two Goes Here</h2><div class="brand"><span class="mark"></span><span class="name">Kradnex</span></div><div class="rule"></div></header>
  <div class="feature-band" style="left:0;width:100px;top:66px;"></div>
  <div class="feature-band" style="left:0;width:86px;top:102px;"></div>
  <div class="feature-band" style="left:0;width:100px;top:137px;"></div>
  <div class="feature-band" style="right:0;width:100px;top:66px;"></div>
  <div class="feature-band" style="right:0;width:86px;top:102px;"></div>
  <div class="feature-band" style="right:0;width:100px;top:137px;"></div>
  <svg class="hub-visual" width="307" height="230" viewBox="0 0 307 230">
    <circle cx="153" cy="118" r="62" fill="none" stroke="#1a9fe0" stroke-width=".8"/>
    <circle cx="153" cy="118" r="56" fill="#1a9fe0"/>
    <g fill="#1a9fe0"><circle cx="104" cy="82" r="2"/><circle cx="92" cy="118" r="2"/><circle cx="104" cy="154" r="2"/><circle cx="202" cy="82" r="2"/><circle cx="214" cy="118" r="2"/><circle cx="202" cy="154" r="2"/></g>
    <rect x="127" y="83" width="53" height="108" rx="5" fill="#1d1d1d"/>
  </svg>
  <div class="phone-screen" role="img" aria-label="Overhead photo of a team working on blueprints at a desk"></div>
  <div class="feature left" style="left:3px;top:68px;"><h3>TITLE HERE</h3><p>Lorem Ipsum is simply dummy text of the printing and typesetting industry. Lorem Ipsum has been the industry's.</p></div>
  <div class="feature left" style="left:-12px;top:104px;"><h3>TITLE HERE</h3><p>Lorem Ipsum is simply dummy text of the printing and typesetting industry. Lorem Ipsum has been the industry's.</p></div>
  <div class="feature left" style="left:3px;top:139px;"><h3>TITLE HERE</h3><p>Lorem Ipsum is simply dummy text of the printing and typesetting industry. Lorem Ipsum has been the industry's.</p></div>
  <div class="feature" style="left:215px;top:68px;"><h3>TITLE HERE</h3><p>Lorem Ipsum is simply dummy text of the printing and typesetting industry. Lorem Ipsum has been the industry's.</p></div>
  <div class="feature" style="left:225px;top:104px;"><h3>TITLE HERE</h3><p>Lorem Ipsum is simply dummy text of the printing and typesetting industry. Lorem Ipsum has been the industry's.</p></div>
  <div class="feature" style="left:215px;top:139px;"><h3>TITLE HERE</h3><p>Lorem Ipsum is simply dummy text of the printing and typesetting industry. Lorem Ipsum has been the industry's.</p></div>
  <footer class="slide-foot"><div class="meta"><svg class="globe" viewBox="0 0 10 10"><circle cx="5" cy="5" r="4.5" fill="#fff"/><circle cx="5" cy="5" r="3.4" fill="#1a9fe0"/><path d="M1.6 5h6.8M5 1.6v6.8M2.4 3.3h5.2M2.4 6.7h5.2" stroke="#fff" stroke-width=".5"/></svg><span>www.kradnex.com</span><span class="sep">|</span><span>Page : 4</span></div></footer>
</article>

<!-- Heading Three -->
<article class="slide col-left row-3">
  <header class="slide-head"><span class="bullet"></span><h2>Heading Three Goes Here</h2><div class="brand"><span class="mark"></span><span class="name">Kradnex</span></div><div class="rule"></div></header>
  <div class="tablet-visual">
    <div class="photo" role="img" aria-label="Photo of a tablet showing an analytics dashboard"></div>
    <div class="frame"></div>
  </div>
  <p class="body-copy copy-three" style="top:56px;">Lorem Ipsum is simply dummy text of the printing and typesetting industry. Lorem Ipsum has been the industry's standard dummy text ever since the 1500s, when an unknown printer took a galley of type and scrambled it to make a type specimen book. It has survived not only five centuries.</p>
  <p class="body-copy copy-three" style="top:109px;">Lorem Ipsum is simply dummy text of the printing and typesetting industry. Lorem Ipsum has been the industry's standard dummy text ever.</p>
  <p class="body-copy copy-three" style="top:140px;">Lorem Ipsum is simply dummy text of the printing and typesetting industry. Lorem Ipsum has been the industry's standard dummy text ever since the 1500s, when an unknown printer took a galley of type and scrambled it to make a type specimen book. It has survived not only five centuries.</p>
  <footer class="slide-foot"><div class="meta"><svg class="globe" viewBox="0 0 10 10"><circle cx="5" cy="5" r="4.5" fill="#fff"/><circle cx="5" cy="5" r="3.4" fill="#1a9fe0"/><path d="M1.6 5h6.8M5 1.6v6.8M2.4 3.3h5.2M2.4 6.7h5.2" stroke="#fff" stroke-width=".5"/></svg><span>www.kradnex.com</span><span class="sep">|</span><span>Page : 5</span></div></footer>
</article>

<!-- Heading Four -->
<article class="slide col-right row-3">
  <header class="slide-head"><span class="bullet"></span><h2>Heading Four Goes Here</h2><div class="brand"><span class="mark"></span><span class="name">Kradnex</span></div><div class="rule"></div></header>
  <div class="map-area" role="img" aria-label="Faint dotted world map"></div>
  <svg class="hub-visual" width="307" height="230" viewBox="0 0 307 230">
    <path d="M30 186 L268 88 L264 80 L283 78 L273 94 L270 91 L36 194 Z" fill="#e2e2e2"/>
    <g fill="#1a9fe0" stroke="#fff" stroke-width="1">
      <circle cx="53" cy="164" r="15"/><circle cx="96" cy="140" r="15"/><circle cx="148" cy="145" r="15"/><circle cx="190" cy="121" r="15"/><circle cx="232" cy="95" r="15"/>
    </g>
    <g fill="none" stroke="#e3137f" stroke-width="1">
      <path d="M53 146v-8M51 140l2-3 2 3"/><path d="M96 122v-8M94 116l2-3 2 3"/><path d="M148 127v-8M146 121l2-3 2 3"/><path d="M190 103v-8M188 97l2-3 2 3"/><path d="M232 77v-8M230 71l2-3 2 3"/>
    </g>
    <g fill="#fff">
      <circle cx="50" cy="159" r="2"/><circle cx="57" cy="159" r="2"/><rect x="48" y="162" width="4" height="8"/><rect x="55" y="162" width="4" height="8"/>
      <rect x="89" y="143" width="3" height="5"/><rect x="94" y="140" width="3" height="8"/><rect x="99" y="137" width="3" height="11"/>
      <circle cx="148" cy="140" r="3"/><path d="M142 152 q6 -9 12 0 z"/>
      <rect x="184" y="114" width="11" height="14" rx="1"/>
      <rect x="226" y="97" width="3" height="5"/><rect x="231" y="94" width="3" height="8"/><rect x="236" y="89" width="3" height="13"/>
    </g>
    <path d="M187 121l2 2 4-4" fill="none" stroke="#1a9fe0" stroke-width="1.2"/>
    <path d="M90 139l5-4 3 2 5-5" fill="none" stroke="#fff" stroke-width="1"/>
  </svg>
  <span class="milestone-title" style="left:33px;top:125px;">Title Here</span>
  <span class="milestone-title" style="left:76px;top:101px;">Title Here</span>
  <span class="milestone-title" style="left:128px;top:106px;">Title Here</span>
  <span class="milestone-title" style="left:170px;top:81px;">Title Here</span>
  <span class="milestone-title" style="left:212px;top:56px;">Title Here</span>
  <footer class="slide-foot"><div class="meta"><svg class="globe" viewBox="0 0 10 10"><circle cx="5" cy="5" r="4.5" fill="#fff"/><circle cx="5" cy="5" r="3.4" fill="#1a9fe0"/><path d="M1.6 5h6.8M5 1.6v6.8M2.4 3.3h5.2M2.4 6.7h5.2" stroke="#fff" stroke-width=".5"/></svg><span>www.kradnex.com</span><span class="sep">|</span><span>Page : 6</span></div></footer>
</article>

</body>
</html>
```